Brightfield Ventures Inc. Letterhead

Creation of attractive and eye catching letterhead for a business start-up for the construction industry. Letterhead must relate to construction, but avoid standard hammer and tools in the design.

I forgot to add some details, sorry about that. Some pertinent info: Ph: 916-555-0187 brightfieldventures.example 448 Willowmere Ave, Ste 210 Folsom, CA 95999 info@brightfieldventures.example not sure if slogan should be in there" “Connecting construction professionals to create a purpose driven industry.” must be able to be used in word. Thanks!

```html
<!DOCTYPE html>
<html lang="en">
<head>
<meta charset="utf-8">
<title>Brightfield Ventures Inc. Letterhead</title>
<link href="https://fonts.googleapis.com/css2?family=Open+Sans:wght@400;600;700&family=Montserrat:wght@600;700&display=swap" rel="stylesheet">
<style>
  :root {
    --backdrop: #e9e9ea;
    --paper: #ffffff;
    --navy: #13215a;
    --red: #c8161d;
    --ink: #3a3a3a;
    --ink-soft: #4a4a4a;
  }
  * { box-sizing: border-box; margin: 0; padding: 0; }
  html, body {
    width: 1200px; height: 784px; overflow: hidden;
    background: var(--backdrop);
  }
  .canvas {
    position: relative; width: 1200px; height: 784px;
  }
  .letterhead {
    position: absolute; left: 338px; top: 22px;
    width: 523px; height: 740px;
    background: var(--paper);
    box-shadow: 0 4px 18px rgba(0,0,0,0.12);
    overflow: hidden;
    font-family: "Open Sans", Arial, sans-serif;
    color: var(--ink);
  }
  .brand {
    position: absolute; left: 42px; top: 46px;
    display: flex; align-items: center; gap: 8px;
  }
  .brand-mark {
    width: 12px; height: 12px; background: var(--red);
  }
  .brand-name {
    font-family: "Montserrat", Arial, sans-serif;
    font-weight: 700; font-size: 15px; letter-spacing: 0.5px;
    color: var(--navy);
  }
  .letter-body {
    position: absolute; left: 70px; top: 150px; width: 395px;
  }
  .salutation {
    font-family: "Montserrat", Arial, sans-serif;
    font-weight: 700; font-size: 12.5px; color: var(--ink-soft);
    margin-bottom: 10px;
  }
  .letter-body p {
    font-size: 10px; line-height: 1.45; color: var(--ink);
    margin-bottom: 14px;
  }
  .signature {
    width: 120px; height: 56px; margin-top: 26px; margin-left: 130px;
    background: linear-gradient(90deg, #e6e6e6, #f4f4f4);
    border-radius: 3px;
  }
  .footer-band {
    position: absolute; left: 0; bottom: 0; width: 100%; height: 30px;
    background: var(--navy);
    display: flex; align-items: center; padding-left: 22px; gap: 18px;
    color: #fff; font-size: 8.5px;
  }
  .footer-item { display: flex; align-items: center; gap: 5px; }
  .footer-item svg { width: 9px; height: 9px; fill: #fff; }
  .web-tab {
    position: absolute; right: 0; bottom: 30px; width: 168px; height: 22px;
  }
  .web-tab svg { position: absolute; inset: 0; }
  .web-tab span {
    position: absolute; right: 14px; top: 5px;
    color: #fff; font-size: 8.5px; font-style: normal;
  }
</style>
</head>
<body>
<div class="canvas">
  <div class="letterhead">
    <div class="brand">
      <div class="brand-mark"></div>
      <div class="brand-name">Brightfield Ventures Inc.</div>
    </div>

    <div class="letter-body">
      <div class="salutation">Dear Mr. Carter,</div>
      <p>Lorem Ipsum is simply dummy text of the printing and typesetting industry. Lorem Ipsum has been the industry's standard dummy text ever since the 1500s, when an unknown printer took a galley of type and scrambled it to make a type specimen book. It has survived not only five centuries, but also the leap into electronic typesetting, remaining essentially unchanged.</p>
      <p>The standard chunk of Lorem Ipsum used since the 1500s is reproduced below for those interested. Sections 1.10.32 and 1.10.33 from "de Finibus Bonorum et Malorum" by Cicero are also reproduced in their exact original form, accompanied by English versions from the 1914 translation by H. Rackham</p>
      <p>Lorem Ipsum is simply dummy text of the printing and typesetting industry. Lorem Ipsum has been the industry's standard dummy text ever since the 1500s, when an unknown printer took a galley of type and scrambled it to make a type specimen book. It has survived not only five centuries, but also the leap into electronic typesetting, remaining essentially unchanged. It was popularised in the</p>
      <p>The standard chunk of Lorem Ipsum used since the 1500s is reproduced below for those interested. Sections 1.10.32 and 1.10.33 from "de Finibus Bonorum et Malorum" by Cicero are also reproduced in their exact original form, accompanied by English versions from the 1914 translation by H. Rackham</p>
      <div class="signature" role="img" aria-label="Handwritten signature"></div>
    </div>

    <div class="web-tab">
      <svg viewBox="0 0 168 22" preserveAspectRatio="none">
        <path d="M0 22 C12 22 12 0 26 0 L168 0 L168 22 Z" fill="var(--red)"/>
      </svg>
      <span>www.brightfieldventures.example</span>
    </div>

    <div class="footer-band">
      <div class="footer-item">
        <svg viewBox="0 0 24 24"><path d="M6.6 10.8c1.4 2.8 3.8 5.1 6.6 6.6l2.2-2.2c.3-.3.7-.4 1-.2 1.1.4 2.3.6 3.6.6.6 0 1 .4 1 1V20c0 .6-.4 1-1 1C10.6 21 3 13.4 3 4c0-.6.4-1 1-1h3.5c.6 0 1 .4 1 1 0 1.3.2 2.5.6 3.6.1.3 0 .7-.2 1L6.6 10.8z"/></svg>
        916-555-0187
      </div>
      <div class="footer-item">
        <svg viewBox="0 0 24 24"><path d="M12 2C8.1 2 5 5.1 5 9c0 5.2 7 13 7 13s7-7.8 7-13c0-3.9-3.1-7-7-7zm0 9.5a2.5 2.5 0 1 1 0-5 2.5 2.5 0 0 1 0 5z"/></svg>
        448 Willowmere Ave, Ste 210, Folsom, CA 95999
      </div>
    </div>
  </div>
</div>
</body>
</html>
```